Dental Office Needs Exciting New Stationary

We need a stationary design that incorporates the logo that we already have and would like to keep the existing color scheme. We need something clean and professional. This is a Endodontic (root canals) office and must represent a dental specialist's office. I need a design for a business card, envelope, and letterhead that all coordinate. I would like the business card to incorporate the information in the business card sample that I am providing. I made the business card design myself but would like to see a better one.
Dental

```html
<!DOCTYPE html>
<html lang="en">
<head>
<meta charset="utf-8">
<title>Harbor Endodontics – Stationery</title>
<link href="https://fonts.googleapis.com/css2?family=Montserrat:wght@600&family=Open+Sans:wght@400;600&display=swap" rel="stylesheet">
<style>
  :root {
    --stage: #ece8e2;
    --paper: #ffffff;
    --brand-blue: #1f6fc0;
    --deep-blue: #1d4ea3;
    --bright-blue: #2a8fd8;
    --band-grey: #7a7b7d;
    --rule-grey: #c9cacc;
    --ink: #3c3d3f;
    --accent: #2a7fd0;
  }
  * { box-sizing: border-box; margin: 0; padding: 0; }
  html, body { width: 1200px; height: 900px; overflow: hidden; }
  body {
    position: relative;
    background: var(--stage);
    font-family: "Open Sans", Arial, sans-serif;
    color: var(--ink);
  }
  .sheet {
    position: absolute;
    background: var(--paper);
    overflow: hidden;
    box-shadow: 0 2px 6px rgba(0,0,0,.18);
  }
  .brand {
    position: absolute;
    display: flex;
    align-items: center;
    gap: 10px;
  }
  .brand-dot {
    width: 28px; height: 28px;
    border-radius: 50%;
    background: var(--brand-blue);
  }
  .brand-rule {
    width: 1px; height: 40px;
    background: var(--rule-grey);
  }
  .brand-name {
    font-family: "Montserrat", Arial, sans-serif;
    font-weight: 600;
    color: var(--brand-blue);
    line-height: 1.05;
    letter-spacing: .3px;
  }
  .contact {
    position: absolute;
    font-size: 9px;
    line-height: 11px;
  }
  .contact b { color: var(--accent); font-weight: 600; }
  .contact-rule {
    position: absolute;
    width: 1px;
    background: var(--rule-grey);
  }
  .footer-band {
    position: absolute;
    left: 0; right: 0; bottom: 0;
    background: var(--band-grey);
  }
  .footer-tab {
    position: absolute;
    right: 0; bottom: 0;
    background: linear-gradient(90deg, var(--bright-blue), var(--deep-blue));
    clip-path: polygon(4% 0, 100% 0, 100% 100%, 0 100%);
    color: #fff;
    font-size: 10px;
    display: flex;
    align-items: center;
    justify-content: center;
  }
  .blue-field {
    background: linear-gradient(90deg, var(--deep-blue) 0%, var(--bright-blue) 50%, var(--deep-blue) 100%);
  }

  /* Letterhead */
  .letterhead { left: 22px; top: 73px; width: 533px; height: 755px; }
  .letterhead .brand { left: 40px; top: 48px; }
  .letterhead .brand-name { font-size: 17px; }
  .letterhead .footer-band { height: 17px; }
  .letterhead .footer-tab { width: 255px; height: 28px; }

  /* Business card front */
  .card-front { left: 573px; top: 133px; width: 299px; height: 169px; }
  .card-front .brand { left: 70px; top: 24px; gap: 8px; }
  .card-front .brand-dot { width: 22px; height: 22px; }
  .card-front .brand-rule { height: 32px; }
  .card-front .brand-name { font-size: 13px; }
  .doctors {
    position: absolute; left: 0; right: 0; top: 73px;
    text-align: center; font-size: 8px; line-height: 10px;
  }
  .doctors .name { color: var(--deep-blue); font-weight: 600; }
  .doctors .note { font-size: 6.5px; }
  .card-front .contact { font-size: 7px; line-height: 9px; }
  .card-front .footer-band { height: 8px; }
  .card-front .footer-tab { width: 142px; height: 14px; font-size: 7.5px; }

  /* Business card back */
  .card-back { left: 883px; top: 135px; width: 292px; height: 165px; }
  .card-back .brand { left: 48px; top: 58px; }
  .card-back .brand-dot { background: #ffffff; }
  .card-back .brand-rule { background: rgba(255,255,255,.55); }
  .card-back .brand-name { font-size: 17px; color: #ffffff; }
  .card-back .web {
    position: absolute; left: 0; right: 0; bottom: 10px;
    text-align: center; color: #ffffff; font-size: 7.5px;
  }

  /* Envelope front */
  .envelope-front { left: 577px; top: 333px; width: 584px; height: 255px; }
  .envelope-front .brand { left: 35px; top: 38px; }
  .envelope-front .brand-name { font-size: 17px; }
  .return-address {
    position: absolute; left: 43px; top: 85px;
    font-size: 8px; line-height: 10px;
  }
  .envelope-front .footer-band { height: 15px; }
  .envelope-front .footer-tab { width: 236px; height: 25px; }

  /* Envelope back */
  .envelope-back { left: 575px; top: 605px; width: 588px; height: 255px; }
  .envelope-back .flap { position: absolute; inset: 0; }
  .envelope-back .seal-dot {
    position: absolute; left: 276px; top: 26px;
    width: 36px; height: 36px; border-radius: 50%;
    background: #ffffff;
  }
</style>
</head>
<body>

<section class="sheet letterhead" aria-label="Letterhead">
  <div class="brand">
    <span class="brand-dot"></span>
    <span class="brand-rule"></span>
    <span class="brand-name">HARBOR<br>ENDODONTICS</span>
  </div>
  <div class="contact" style="left:263px; top:48px;">
    <b>O</b> : 555.210.4470<br>
    <b>F</b> : 555.210.4481<br>
    840 Linden Street<br>
    Riverton, CA 95001
  </div>
  <span class="contact-rule" style="left:364px; top:48px; height:44px;"></span>
  <div class="contact" style="left:382px; top:48px;">
    <b>O</b> : 555.318.2290<br>
    <b>F</b> : 555.318.2295<br>
    2150 Oakmont ave. Suite #4<br>
    Fairbrook, CA 95002
  </div>
  <div class="footer-band"></div>
  <div class="footer-tab">www.harborendodontics.com</div>
</section>

<section class="sheet card-front" aria-label="Business card, front">
  <div class="brand">
    <span class="brand-dot"></span>
    <span class="brand-rule"></span>
    <span class="brand-name">HARBOR<br>ENDODONTICS</span>
  </div>
  <div class="doctors">
    <span class="name">Daniel R Mercer</span> | DDS MS<br>
    <span class="name">Lucas M Ortega</span> | DDS<br>
    <span class="note">Practice Limited to Endodontics</span>
  </div>
  <div class="contact" style="left:60px; top:111px; text-align:right; width:68px;">
    <b>O</b> : 555.210.4470<br>
    <b>F</b> : 555.210.4481<br>
    <br>
    840 Linden Street<br>
    Riverton, CA 95001
  </div>
  <span class="contact-rule" style="left:150px; top:110px; height:40px;"></span>
  <div class="contact" style="left:170px; top:111px;">
    <b>O</b> : 555.318.2290<br>
    <b>F</b> : 555.318.2295<br>
    <br>
    2150 Oakmont ave. Suite #4<br>
    Fairbrook, CA 95002
  </div>
  <div class="footer-band"></div>
  <div class="footer-tab">www.harborendodontics.com</div>
</section>

<section class="sheet card-back blue-field" aria-label="Business card, back">
  <div class="brand">
    <span class="brand-dot"></span>
    <span class="brand-rule"></span>
    <span class="brand-name">HARBOR<br>ENDODONTICS</span>
  </div>
  <div class="web">www.harborendodontics.com</div>
</section>

<section class="sheet envelope-front" aria-label="Envelope, front">
  <div class="brand">
    <span class="brand-dot"></span>
    <span class="brand-rule"></span>
    <span class="brand-name">HARBOR<br>ENDODONTICS</span>
  </div>
  <div class="return-address">
    840 Linden Street Riverton, CA 95001<br>
    2150 Oakmont ave. Suite #4 Fairbrook, CA 95002
  </div>
  <div class="footer-band"></div>
  <div class="footer-tab">www.harborendodontics.com</div>
</section>

<section class="sheet envelope-back blue-field" aria-label="Envelope, back">
  <svg class="flap" width="588" height="255" viewBox="0 0 588 255" aria-hidden="true">
    <path d="M0 2 C 120 20, 220 70, 294 88 C 368 70, 468 20, 588 2"
          fill="rgba(255,255,255,0.06)" stroke="rgba(10,40,110,0.45)" stroke-width="1.2"/>
  </svg>
  <span class="seal-dot"></span>
</section>

</body>
</html>
```